International Clinical Software Company needs a new business card design

We are looking for a new business card design for our company that has recently expanded into the UK market, making us a multinational company.
After having rebranded our website and produced a new style guide, we are looking for a business card that is creative and attention grabbing, while being consistent with the style and colour scheme used on the new website, www.plumvora.example
We produce care management technology for the aged care market, but the main aspect we aim to communicate is the human element of our software, and the way it assists in providing better care for aged people, and stronger relationships between aged people and the staff that care for them.
Our current business card is a dark green with gold text, which makes the text quite difficult to read, not very aesthetically appealing and the colour scheme looks quite dated.
We would like something fresh and modern, that can still be colourful but doesn't use large blocks of dark colour, and uses the colours within our logo.
Something tying in with the leaves that are used in our logo could work quite nicely, along with the Autumn/Fall colours of soft greens, yellows and reds (also in our existing logo). However also happy to look at fresh, completely out of the box ideas we may not have yet considered.
Target Market(s)
The people that receive this business card work in the aged card or health industry and are either corporate/management level staff or clinical (Registered Nurses, care workers etc.)
Industry/Entity Type
Health Product
Contact Information for Business Card
Company Name - BrindlewayCare
Company locations: United Kingdom, Australia, New Zealand
Staff Details:
Staff name: Derek Mallow
Staff job title: Executive Chairman
Staff email: d.mallow@plumvora.example
Office phone number: 01742 918576
Font styles to use
Other font styles liked:
- Calibri
Requirements
Must have
- Must include the BrindlewayCare brand name in it's current font
- Must include logo (3 leaves in gold circle)
- Must include Business Card Details
Nice to have
- Elements of gold
- White space
- Something autumn themed but not too cliched
Should not have
- No blue - used by a major competitor and we would like to differentiate from them
- Large blocks of dark green colour (the green that appears in our leaves on the logo on our current business card is the background colour and it is far too dark)

```html
<!DOCTYPE html>
<html lang="en">
<head>
<meta charset="utf-8">
<title>BrindlewayCare business card</title>
<link rel="stylesheet" href="https://fonts.googleapis.com/css2?family=Carlito:wght@400;700&display=swap">
<style>
  :root {
    --canvas: #ecebe8;
    --card-white: #ffffff;
    --paper: #f8f6f2;
    --gold: #a8966a;
    --gold-text: #a28f63;
    --crimson: #8c0026;
    --ink-light: #ffffff;
    --leaf-red: #c2401c;
    --leaf-orange: #e98a1f;
    --leaf-yellow: #e8c22a;
    --leaf-green: #6f7d22;
  }
  * { box-sizing: border-box; margin: 0; padding: 0; }
  html, body { width: 1200px; height: 900px; overflow: hidden; }
  body {
    position: relative;
    background: var(--canvas);
    font-family: "Carlito", "Calibri", sans-serif;
  }
  .card {
    position: absolute;
    box-shadow: 0 6px 18px rgba(0,0,0,0.18);
    overflow: hidden;
  }
  .card--front {
    left: 77px; top: 35px; width: 588px; height: 362px;
    background: var(--card-white);
  }
  .card--back {
    left: 388px; top: 507px; width: 567px; height: 350px;
    background: var(--paper);
  }
  .card__shapes { position: absolute; inset: 0; }
  .brand {
    position: absolute;
    display: flex; align-items: center;
    color: var(--gold-text);
    font-weight: 400;
    white-space: nowrap;
  }
  .brand--front { left: 119px; top: 48px; font-size: 44px; gap: 14px; }
  .brand__mark {
    width: 84px; height: 84px; border-radius: 50%;
    border: 3px solid var(--gold);
    flex: none;
  }
  .brand--back { left: 40px; top: 56px; font-size: 46px; }
  .person {
    position: absolute; right: 334px; top: 243px;
    text-align: right; color: var(--ink-light);
  }
  .person__name { font-size: 23px; font-weight: 700; line-height: 28px; }
  .person__title { font-size: 17px; line-height: 22px; }
  .locations {
    position: absolute; left: 306px; top: 243px;
    color: var(--ink-light); font-size: 17px; line-height: 24px;
  }
  .contact {
    position: absolute; left: 198px; top: 306px;
    display: flex; align-items: center; gap: 8px;
    color: var(--ink-light); font-size: 16px;
  }
  .contact svg { width: 12px; height: 12px; }
</style>
</head>
<body>
  <section class="card card--front">
    <svg class="card__shapes" viewBox="0 0 588 362" aria-hidden="true">
      <polygon points="0,199 403,199 385,223 0,223" fill="var(--crimson)"/>
      <polygon points="0,227 391,227 414,191 588,191 588,362 0,362" fill="var(--gold)"/>
    </svg>
    <div class="brand brand--front">
      <span class="brand__mark"></span>
      <span class="brand__name">BrindlewayCare</span>
    </div>
    <div class="person">
      <p class="person__name">Derek Mallow</p>
      <p class="person__title">Executive Chairman</p>
    </div>
    <div class="locations">
      <p>United Kingdom, Australia</p>
      <p>New Zealand</p>
    </div>
    <div class="contact">
      <svg viewBox="0 0 24 24" aria-hidden="true"><path fill="#fff" d="M6.6 10.8a15.2 15.2 0 0 0 6.6 6.6l2.2-2.2a1 1 0 0 1 1-.25 11.4 11.4 0 0 0 3.6.6 1 1 0 0 1 1 1V20a1 1 0 0 1-1 1A17 17 0 0 1 3 4a1 1 0 0 1 1-1h3.5a1 1 0 0 1 1 1c0 1.25.2 2.45.6 3.6a1 1 0 0 1-.25 1z"/></svg>
      <span>d.mallow@plumvora.example</span>
    </div>
  </section>

  <section class="card card--back">
    <svg class="card__shapes" viewBox="0 0 567 350">
      <defs>
        <linearGradient id="leaf-tones" x1="0" y1="1" x2="1" y2="0">
          <stop offset="0" stop-color="var(--leaf-red)"/>
          <stop offset="0.35" stop-color="var(--leaf-orange)"/>
          <stop offset="0.6" stop-color="var(--leaf-yellow)"/>
          <stop offset="0.8" stop-color="var(--leaf-orange)"/>
          <stop offset="1" stop-color="var(--leaf-red)"/>
        </linearGradient>
      </defs>
      <path role="img" aria-label="Illustration of scattered autumn leaves in red, orange, yellow and green"
            d="M567,12 L567,350 L0,350 L0,258 C150,252 280,240 340,215 C370,190 380,160 410,140 C440,90 490,30 567,12 Z"
            fill="url(#leaf-tones)" opacity="0.9"/>
    </svg>
    <div class="brand brand--back">
      <span class="brand__name">BrindlewayCare</span>
    </div>
  </section>
</body>
</html>
```